Meadowlark Property Review is a leading provider of residential appraisal and home inspection products in S

I need a business card/logo designed that obviously describes my business. We are a residential appraisal and home inspection company in Springfield, MO. We offer residential appraisals, home inspection, pest inspection and radon gas measurement. We have been in business for 18 years and hold state certified residential appraisal licenses and OBREX certified home inspection licenses. I have a logo that I really like and will attach, but would be open to new suggestions. I like more modern designs than traditional and would like a two sided card with our services, licenses and qualifications on the back.

```html
<!DOCTYPE html>
<html lang="en">
<head>
<meta charset="utf-8">
<title>Meadowlark Property Review – Business Card</title>
<link rel="stylesheet" href="https://fonts.googleapis.com/css2?family=Source+Sans+3:ital,wght@0,400;0,600;1,400&display=swap">
<style>
  :root {
    --stage: #3b3b3b;
    --brown: #8b6b43;
    --orange: #ee8a1c;
    --paper: #f7f7f7;
    --ink: #4a4a4a;
    --white: #ffffff;
  }
  * { margin: 0; padding: 0; box-sizing: border-box; }
  html, body { width: 1200px; height: 750px; overflow: hidden; }
  body {
    background: var(--stage);
    font-family: "Source Sans 3", sans-serif;
    position: relative;
  }
  .card {
    position: absolute;
    top: 228px;
    width: 461px;
    height: 262px;
    overflow: hidden;
  }
  .card--front { left: 124px; background: var(--brown); }
  .card--back { left: 618px; background: var(--brown); }

  .front-shape { position: absolute; inset: 0; width: 461px; height: 262px; }

  .brand {
    position: absolute;
    left: 40px;
    top: 44px;
    display: flex;
    align-items: center;
    gap: 8px;
    color: var(--brown);
    font-weight: 600;
    font-size: 17px;
    line-height: 1.1;
  }
  .brand__mark { width: 12px; height: 12px; background: var(--orange); flex: none; }

  .address {
    position: absolute;
    left: 39px;
    top: 124px;
    font-size: 11.5px;
    line-height: 14.5px;
    color: var(--ink);
  }
  .contacts {
    position: absolute;
    left: 40px;
    top: 162px;
    list-style: none;
    font-size: 11.5px;
    color: var(--ink);
  }
  .contacts li { display: flex; align-items: center; gap: 6px; height: 17.6px; }
  .contacts svg { width: 12px; height: 12px; fill: var(--brown); flex: none; }

  .person {
    position: absolute;
    right: 75px;
    top: 95px;
    text-align: right;
  }
  .person__name { color: var(--brown); font-weight: 600; font-size: 17px; line-height: 20px; }
  .person__role { color: var(--orange); font-size: 13px; line-height: 16px; }

  .back-brand {
    position: absolute;
    left: 0; right: 0;
    top: 102px;
    display: flex;
    justify-content: center;
    align-items: center;
    gap: 10px;
    color: var(--white);
    font-weight: 600;
    font-size: 22px;
  }
  .back-brand__mark { width: 14px; height: 14px; background: var(--orange); }

  .services {
    position: absolute;
    left: 0; right: 0;
    top: 200px;
    text-align: center;
    color: var(--white);
    font-style: italic;
    font-size: 12px;
    line-height: 18px;
  }
  .services__dot { color: var(--orange); font-style: normal; }
</style>
</head>
<body>

<section class="card card--front">
  <svg class="front-shape" viewBox="0 0 461 262" aria-hidden="true">
    <path d="M0,0 H364 C432,48 448,176 358,262 H0 Z" fill="var(--paper)"/>
    <path d="M240,262 C344,232 408,176 419,102 C424,168 400,224 354,262 Z" fill="var(--orange)"/>
  </svg>

  <div class="brand">
    <span class="brand__mark"></span>
    <span>Meadowlark<br>Property Review</span>
  </div>

  <p class="address">412 Larkspur Court<br>Brookfield, Missouri 64628</p>

  <ul class="contacts">
    <li>
      <svg viewBox="0 0 12 12"><path d="M2.5 0.8 L4.3 0.8 L5 3.4 L3.8 4.4 C4.4 5.8 5.9 7.4 7.4 8.1 L8.5 6.9 L11.2 7.6 L11.2 9.4 C11.2 10.4 10.4 11.2 9.4 11.2 C4.9 10.9 1.1 7.1 0.8 2.6 C0.8 1.6 1.5 0.8 2.5 0.8 Z"/></svg>
      417 555 0182
    </li>
    <li>
      <svg viewBox="0 0 12 12"><rect x="3" y="1" width="6" height="3"/><rect x="0.5" y="4.5" width="11" height="5" rx="1"/><rect x="3" y="8" width="6" height="3" fill="var(--paper)" stroke="var(--brown)"/></svg>
      417 555 0196
    </li>
    <li>
      <svg viewBox="0 0 12 12"><path d="M0.5 2.5 H11.5 V9.5 H0.5 Z M1.5 3.3 L6 6.6 L10.5 3.3" fill="none" stroke="var(--brown)" stroke-width="1.2"/></svg>
      office@meadowlarkpr.com
    </li>
    <li>
      <svg viewBox="0 0 12 12"><circle cx="6" cy="6" r="5.5"/><path d="M3 3.5 C4.5 3 5 4.5 4 5.5 C5 7 6.5 6 6.5 8 L5.5 10 M8 2.5 C7 3.5 8.5 4.5 9.5 4" fill="none" stroke="var(--paper)" stroke-width="1"/></svg>
      www.meadowlarkpr.com
    </li>
  </ul>

  <div class="person">
    <p class="person__name">Daniel Harper</p>
    <p class="person__role">CEO/Founder</p>
  </div>
</section>

<section class="card card--back">
  <div class="back-brand">
    <span class="back-brand__mark"></span>
    <span>Meadowlark Property Review</span>
  </div>
  <p class="services">
    Residential appraisals <span class="services__dot">•</span> Home inspection<br>
    Pest inspection and radon gas measurement.
  </p>
</section>

</body>
</html>
```